Sleek, luxurious B&W packaging for sensual new massager product

We require packaging for our new product, a sleek new massager wand. The packaging needs to be black and white, and needs to represent our brand. The words to describe our brand are:

Sensual
Luxurious
Sleek simplicity

Here is a Pinboardly board detailing our preferred style: https://uk.pinboardly.example/moravtenley/packaging-velorine/

We love the stand out simplicity of Duvree packaging, for example.

Further details and requirements are attached.

Target Market(s)

Female, 18-55yo.

Industry/Entity Type

Fashion

Font styles to use
Sans Serif

Colors
000000
ffffff

Requirements
Must have
• See attached for explanation of requirements.
• DETAILED REQUIREMENTS
• BOX FRONT:
• LOGO
• CORDLESS MINI WAND MASSAGER
• www.quelvoro.example
• BOX SIDE 1:
• ICON
• Sleek, Cordless design
• ICON
• 100% Waterproof
• ICON
• USB Rechargable
• ICON
• 8x Stimulating Speeds
• ICON
• 20x Heavenly Pulsations
• ICON
• Discreetly Quiet
• ICON
• Body-safe Silicone
• ICON
• Phthalate-free
• BOX SIDE 2
• The Velorine was created for your theraputic satisfaction.
• Delight your body with 8 Stimulating Speeds & 20 Heavenly Pulsations of Massage Pleasure.
• Where will Velorine take you?
• LOGO
• www.quelvoro.example
• BOX BASE:
• Colour: Aubergine
• Size: 7.8” (L) x 1.6” (W) / 200MM (L) x 41MM (W)
• Weight: 6.5 ounces / 186G
• Material: Body-Safe Medical Grade Silicone + ABS
• Battery: Li-oh 1200MAH 3.7V
• Charging: 1.5 hours at 5V 500MA
• Sound Output: =<40DB
• User time: up to 3 hours
• Model: 00000000-000000000
• LOGO
• www.quelvoro.example
• 1 year warranty (ICON)
• CE logo + barcode (awaiting)
Nice to have
• Sleek, luxury, black and white design.
• Here's our pinboardly board of ideas: https://uk.pinboardly.example/moravtenley/packaging-velorine/
• I am open to both a landscape or portrait box design. Possibly portrait looks more elegant.
Should not have
• Too much text.
• Too much fussiness.

```html
<!DOCTYPE html>
<html lang="en">
<head>
<meta charset="utf-8">
<title>Velorine by Quelvoro – Packaging</title>
<link href="https://fonts.googleapis.com/css2?family=Open+Sans:wght@300;400;800&display=swap" rel="stylesheet">
<style>
  :root{
    --ink:#000000;
    --paper:#ffffff;
    --stage:#f1f1f1;
  }
  *{box-sizing:border-box;margin:0;padding:0}
  html,body{width:1200px;height:861px;overflow:hidden}
  body{background:var(--stage);font-family:"Open Sans",sans-serif;color:var(--ink);position:relative}

  .panel{position:absolute;left:100px;width:1000px;height:250px;background:var(--paper);overflow:hidden;box-shadow:0 2px 10px rgba(0,0,0,.08)}
  .panel--front{top:150px}
  .panel--side{top:461px}

  /* black bands */
  .band{position:absolute;background:var(--ink)}
  .panel--front .band--left{left:0;top:0;width:18px;height:250px}
  .panel--front .band--right{right:0;bottom:0;width:320px;height:18px}
  .panel--front .band--bottom{left:0;bottom:0;width:300px;height:18px}
  .panel--side .band--left{left:0;top:0;width:18px;height:250px}
  .panel--side .band--top{left:0;top:0;width:300px;height:18px}
  .panel--side .band--right{right:0;top:0;width:18px;height:250px}

  .brand{position:absolute;left:0;right:0;top:58px;text-align:center}
  .brand__name{font-weight:300;font-size:42px;letter-spacing:.06em;line-height:1}
  .brand__by{font-weight:300;font-size:11px;letter-spacing:.45em;margin-top:8px;color:#444}
  .brand__product{font-weight:400;font-size:13px;letter-spacing:.12em;margin-top:16px}
  .brand__url{font-weight:400;font-size:12px;letter-spacing:.3em;margin-top:12px}

  .features{position:absolute;left:60px;right:50px;top:60px;display:flex;justify-content:space-between;list-style:none}
  .feature{width:100px;display:flex;flex-direction:column;align-items:center;text-align:center}
  .feature__icon{width:46px;height:46px;display:flex;align-items:center;justify-content:center}
  .feature__icon svg{width:42px;height:42px}
  .feature__si{font-weight:800;font-size:32px;line-height:46px}
  .feature__label{margin-top:10px;font-weight:800;font-size:10px;line-height:1.15;letter-spacing:.04em;text-transform:uppercase}
</style>
</head>
<body>

<section class="panel panel--front" aria-label="Box front">
  <div class="band band--left"></div>
  <div class="band band--bottom"></div>
  <div class="band band--right"></div>
  <div class="brand">
    <p class="brand__name">Velorine</p>
    <p class="brand__by">BY QUELVORO</p>
    <p class="brand__product">CORDLESS MINI WAND MASSAGER</p>
    <p class="brand__url">www.quelvoro.example</p>
  </div>
</section>

<section class="panel panel--side" aria-label="Box side">
  <div class="band band--left"></div>
  <div class="band band--top"></div>
  <div class="band band--right"></div>
  <ul class="features">
    <li class="feature">
      <span class="feature__icon"><svg viewBox="0 0 40 40"><circle cx="20" cy="20" r="16" fill="none" stroke="#000" stroke-width="4"/><rect x="14" y="12" width="12" height="12" rx="2" fill="#000"/><rect x="16" y="8" width="2" height="5" fill="#000"/><rect x="22" y="8" width="2" height="5" fill="#000"/><rect x="19" y="24" width="2" height="8" fill="#000"/></svg></span>
      <span class="feature__label">Sleek<br>Cordless<br>Design</span>
    </li>
    <li class="feature">
      <span class="feature__icon"><svg viewBox="0 0 40 40"><path d="M20 5 C 26 15 31 21 31 27 A 11 11 0 0 1 9 27 C 9 21 14 15 20 5Z" fill="#000"/><line x1="2" y1="25" x2="38" y2="25" stroke="#000" stroke-width="1.5"/></svg></span>
      <span class="feature__label">100%<br>Waterproof</span>
    </li>
    <li class="feature">
      <span class="feature__icon"><svg viewBox="0 0 40 40"><rect x="11" y="6" width="18" height="31" rx="2" fill="none" stroke="#000" stroke-width="3"/><rect x="16" y="2" width="8" height="4" fill="#000"/><path d="M20 12v16M20 12l-3 4M20 12l3 4M20 22l-4-3M20 24l4-3" stroke="#000" stroke-width="2" fill="none"/></svg></span>
      <span class="feature__label">USB<br>Rechargable</span>
    </li>
    <li class="feature">
      <span class="feature__icon"><svg viewBox="0 0 40 40"><path d="M3 30 A17 17 0 0 1 37 30Z" fill="#000"/><path d="M20 30 L20 13 M20 30 L9 19 M20 30 L31 19 M20 30 L5 27 M20 30 L35 27" stroke="#fff" stroke-width="1.5"/></svg></span>
      <span class="feature__label">8x Stimulating<br>Speeds</span>
    </li>
    <li class="feature">
      <span class="feature__icon"><svg viewBox="0 0 40 40"><path d="M3 26 C 10 26 10 10 17 10 S 20 30 26 30 S 30 12 37 14" fill="none" stroke="#000" stroke-width="3"/><path d="M10 30 C 14 30 15 16 20 16 S 26 28 31 24" fill="none" stroke="#000" stroke-width="1.5"/></svg></span>
      <span class="feature__label">20x Heavenly<br>Pulsations</span>
    </li>
    <li class="feature">
      <span class="feature__icon"><svg viewBox="0 0 40 40"><circle cx="20" cy="20" r="16" fill="none" stroke="#000" stroke-width="3.5"/><path d="M12 17h5l6-5v16l-6-5h-5z" fill="#000"/><line x1="10" y1="30" x2="30" y2="10" stroke="#000" stroke-width="3"/></svg></span>
      <span class="feature__label">Discreetly<br>Quiet</span>
    </li>
    <li class="feature">
      <span class="feature__icon"><span class="feature__si">Si</span></span>
      <span class="feature__label">Body-Safe<br>Silicone</span>
    </li>
    <li class="feature">
      <span class="feature__icon"><svg viewBox="0 0 40 40"><circle cx="20" cy="20" r="17" fill="#000"/><path d="M12 28 C 12 18 18 11 29 11 C 29 22 22 28 12 28Z" fill="#fff"/><line x1="12" y1="28" x2="24" y2="16" stroke="#000" stroke-width="1.5"/></svg></span>
      <span class="feature__label">Phthalate<br>Free</span>
    </li>
  </ul>
</section>

</body>
</html>
```